Business card por a urban DJ, up scale audience target

Need a sober design, modern, conservative colors but i can consider some options, y play rnb, hip hop, EDM and top40.

Business card for contact and personal info, double sided, use logo attrached please; im 42 so i need a card acording to my age an target audience.

Target Market(s)

Adult people, up scale audience

Industry/Entity Type

Music Download

Contact Information for Business Card

Cel (318) 4207265518 www.lumadrift.com

Requirements
Must have
• open mind
Nice to have
• open mind
Should not have
• DJ

```html
<!DOCTYPE html>
<html lang="en">
<head>
<meta charset="UTF-8">
<title>Luma – Business Card</title>
<link rel="stylesheet" href="https://fonts.googleapis.com/css2?family=Open+Sans:wght@400;600;800&display=swap">
<style>
  :root {
    --backdrop: #2e2e2e;
    --card: #050505;
    --logo-grey: #c4c4c4;
    --eq-grey: #6a6a6a;
    --text-light: #e6e6e6;
    --text-dim: #a8a8a8;
    --rule: #5a5a5a;
  }
  * { margin: 0; padding: 0; box-sizing: border-box; }
  html, body {
    width: 1200px; height: 900px; overflow: hidden;
    background: var(--backdrop);
    font-family: "Open Sans", sans-serif;
  }
  .stage {
    width: 1200px; height: 900px;
    display: flex; flex-direction: column; align-items: center; justify-content: center;
    gap: 36px;
  }
  .card {
    position: relative;
    width: 700px; height: 400px;
    background: var(--card);
    overflow: hidden;
    box-shadow: 0 10px 30px rgba(0,0,0,.45);
  }
  .equalizer {
    position: absolute;
    background: linear-gradient(to top, var(--eq-grey) 0%, rgba(106,106,106,.75) 55%, rgba(106,106,106,0) 100%);
  }
  .card-front .equalizer { left: 0; right: 0; bottom: 0; height: 190px; }
  .card-back .equalizer { left: 90px; right: 0; bottom: 0; height: 150px; }

  .brand-name {
    position: absolute;
    display: flex; align-items: center; gap: 18px;
    color: var(--logo-grey);
    font-weight: 800;
    letter-spacing: 4px;
    line-height: 1;
  }
  .brand-mark { background: var(--logo-grey); }
  .card-front .brand-name { left: 232px; top: 74px; font-size: 104px; }
  .card-front .brand-mark { width: 26px; height: 26px; }
  .card-back .brand-name { right: 56px; top: 48px; font-size: 72px; }
  .card-back .brand-mark { width: 18px; height: 18px; }

  .divider {
    position: absolute; left: 0; right: 0; top: 212px;
    height: 1px; background: var(--rule);
  }
  .contact {
    position: absolute; left: 46px; bottom: 38px; z-index: 1;
  }
  .contact-name { color: var(--text-light); font-weight: 600; font-size: 22px; }
  .contact-role { color: var(--text-dim); font-size: 12px; margin-bottom: 10px; }
  .contact-line {
    display: flex; align-items: center; gap: 8px;
    color: var(--text-dim); font-size: 15px; line-height: 1.45;
  }
  .contact-line svg { width: 12px; height: 12px; flex: none; }
</style>
</head>
<body>
<main class="stage">
  <section class="card card-front">
    <div class="equalizer" role="img" aria-label="Grey equalizer block pattern rising along the bottom"></div>
    <div class="brand-name"><span class="brand-mark"></span>LUMA</div>
  </section>

  <section class="card card-back">
    <div class="brand-name"><span class="brand-mark"></span>LUMA</div>
    <div class="divider"></div>
    <div class="equalizer" role="img" aria-label="Grey equalizer block pattern along the bottom"></div>
    <div class="contact">
      <p class="contact-name">Marco Vell</p>
      <p class="contact-role">CEO</p>
      <p class="contact-line">
        <svg viewBox="0 0 12 12"><rect x="3" y="0.5" width="6" height="11" rx="1" fill="none" stroke="#a8a8a8" stroke-width="1"/><rect x="5" y="9.2" width="2" height="1" fill="#a8a8a8"/></svg>
        (318) 4207265518
      </p>
      <p class="contact-line">
        <svg viewBox="0 0 12 12"><circle cx="6" cy="6" r="5.2" fill="none" stroke="#a8a8a8" stroke-width="1"/><ellipse cx="6" cy="6" rx="2.2" ry="5.2" fill="none" stroke="#a8a8a8" stroke-width="1"/><line x1="0.8" y1="6" x2="11.2" y2="6" stroke="#a8a8a8" stroke-width="1"/></svg>
        www.lumadrift.com
      </p>
    </div>
  </section>
</main>
</body>
</html>
```